Fine Art business needs new website

We need a simple website with a home page, about us page, New sculptures, Sold sculptures, and a contact us page.Our sculptures are very high end one of a kind pieces. As such we need the site to be VERY elegant and professional. Lastly, because I'll be updating pictures on the website on a monthly basis it needs to be user friendly to update (Wordpress is preferred). The only branding we have so far for the business is a business card.
Updates
I wasn't completely ready when this project launched, also I am on the road right now and haven't been able to be as responsive to all you designers as I would like. I will work on giving feedback to all the top designs we've received so far. Thank you all so much for your participation and hardwork.
Target Market(s)
High end customers (affluent), art collectors, interior decorators/designers
Industry/Entity Type
Art Gallery
Coding
Coded - Design and coding required
Number of Pages Required
5+ page
Requirements
Must have
- Easily editable picture gallery for myself so that I can add new pieces(pictures of the pieces), remove sold pieces, etc. I would like the website to be built in wordpress so I can update it. I currently use mangewordpress through Netmarro for my other business website and would like to do the same for this one.
- Pages:
- -Intro page with featured pieces
- -Current pieces gallery (for sale) mainly a picture gallery
- -Sculptures archive (sold pieces) another picture gallery
- -About us: Pull-down of -about the artist (attached content)
- -Artistic Process (attached content)
- -Show Schedule:
- -one page dedicated to "friends of TMV" (basically a link page)
- TO BE CLEAR "www.pineroverslane.com" IS A TOTALLY DIFFERENT SITE AND I'M NOT TRYING TO COMBINE THE TWO OR JOIN THEM INTO ONE. This page needs be more elegant and seperate from the Pine Rovers site.
- UPDATE: I'd like a link to the TMV Facebook page: https://www.faceplume-social.com/mirelcraftworks/
Nice to have
- I would like the pictures on the gallery pages able to have text connected with them (Materials, price)
- I would like the site style and fonts to be similar to our business cards we've already had designed (picture attached).
Should not have
- Too much flash or other things that will make the site slow to load.

```html
<!DOCTYPE html>
<html lang="en">
<head>
<meta charset="utf-8">
<title>Tidemark Vale Studios</title>
<link href="https://fonts.googleapis.com/css2?family=Marcellus&family=Raleway:wght@400;500;700;800&display=swap" rel="stylesheet">
<style>
:root{
  --ink:#0c0c0c;
  --char:#1d1d1d;
  --slate:#2c2c2c;
  --stone:#3a3a3a;
  --white:#ffffff;
  --soft:#e6e6e6;
  --muted:#6a6a6a;
  --frame:#bdb6b6;
  --rule:#555555;
}
*{margin:0;padding:0;box-sizing:border-box}
html,body{width:1200px;height:3390px;overflow:hidden;background:var(--ink)}
body{font-family:"Raleway",sans-serif;color:var(--white);position:relative}
section,header,footer{position:absolute;left:0;width:1200px;overflow:hidden}
.abs{position:absolute}
h1,h2{font-family:"Marcellus",serif;font-weight:400;text-transform:uppercase}
.btn{position:absolute;display:flex;align-items:center;justify-content:center;border:2px solid var(--white);color:var(--white);text-decoration:none;font-size:15px;font-weight:500;outline:2px solid rgba(0,0,0,.6);outline-offset:-6px}
.btn--caps{text-transform:uppercase;font-family:"Marcellus",serif;font-size:15px}
.body-copy{font-size:13.5px;line-height:29px;text-align:justify;color:var(--soft)}
.body-copy p+p{margin-top:16px}
.bar-heading{position:absolute;font-size:33px;padding-left:22px;border-left:3px solid var(--white);line-height:36px}
.center-heading{position:absolute;left:0;width:1200px;text-align:center;font-size:33px}
.underline{position:absolute;left:562px;width:76px;height:3px;background:var(--white)}
.arrow{position:absolute;width:32px;height:60px}

/* hero */
.hero{top:0;height:620px;background:linear-gradient(180deg,#151515,#202020 60%,#1a1a1a)}
.brand{position:absolute;left:0;top:0;width:345px;height:205px}
.brand-name{position:absolute;left:20px;top:140px;width:260px;text-align:center;font-family:"Marcellus",serif;font-size:14px;letter-spacing:2px;color:var(--muted);text-transform:uppercase}
.nav{position:absolute;top:30px;right:100px;display:flex;gap:40px;font-size:15px;font-weight:500}
.nav a{color:var(--white);text-decoration:none}
.hero h1{position:absolute;left:98px;top:280px;font-size:45px;letter-spacing:1px}
.hero p{position:absolute;left:100px;top:362px;width:600px;font-size:15px;line-height:26px}
.hero-piece{position:absolute;left:790px;top:70px;width:290px;height:550px}
/* about */
.about{top:620px;height:530px;background:linear-gradient(180deg,#262626,#1c1c1c);border-top:2px solid #3c3c3c}
.photo-frame{position:absolute;border:6px solid var(--stone)}
.frame-light{border:4px solid var(--frame)}
/* gallery */
.gallery{top:1150px;height:730px;background:linear-gradient(180deg,#3b3b3b,#2d2d2d)}
.card{position:absolute;top:198px;width:310px;height:345px}
.card-title{position:absolute;top:378px;left:0;width:310px;text-align:center;font-weight:800;font-size:18px}
.card-price{position:absolute;top:420px;left:0;width:310px;text-align:center;font-weight:700;font-size:20px}
/* videos */
.videos{top:1880px;height:525px;background:linear-gradient(180deg,#252525,#1d1d1d)}
/* testimonials */
.testimonials{top:2405px;height:530px}
.vline{position:absolute;left:599px;width:2px;background:var(--soft)}
.quote{position:absolute;left:160px;top:195px;width:880px;text-align:center;font-size:14px;line-height:27px;color:var(--soft)}
.quote-name{position:absolute;left:0;top:276px;width:1200px;text-align:center;font-weight:800;font-size:16px}
/* contact */
.contact{top:2935px;height:455px;background:var(--ink);border-top:2px solid #333}
.contact-row{position:absolute;top:192px;left:0;width:1200px;display:flex;justify-content:center;gap:46px;font-size:18px}
.contact-item{display:flex;align-items:center;gap:12px}
.foot-nav{position:absolute;top:290px;left:0;width:1200px;display:flex;justify-content:center;gap:22px;font-size:14px;font-weight:700;text-transform:uppercase}
.foot-nav span.sep{font-weight:400}
.foot-rule{position:absolute;left:98px;top:364px;width:1004px;height:1px;background:var(--rule)}
.copyright{position:absolute;left:98px;top:400px;font-size:13px;color:var(--soft)}
.social{position:absolute;right:98px;top:392px;display:flex;gap:9px}
.social span{width:34px;height:34px;border:2px solid var(--white);border-radius:50%}
</style>
</head>
<body>

<header class="hero">
  <svg class="brand" viewBox="0 0 345 205" aria-hidden="true">
    <polygon points="0,0 345,0 270,205 0,205" fill="#8a8a8a"/>
    <polygon points="0,0 335,0 262,197 0,197" fill="#ffffff"/>
  </svg>
  <div class="brand-name">Tidemark Vale Studios</div>
  <nav class="nav">
    <a href="#">Home</a><a href="#">About Us</a><a href="#">New Sculptures</a><a href="#">Sold Sculptures</a><a href="#">Contact Us</a>
  </nav>
  <h1>Tidemark Vale Studios</h1>
  <p>Nemo enim ipsam voluptatem quia voluptas sit aspernatur aut odit aut fugit, sed quia consequuntur magni dolores.</p>
  <a class="btn" href="#" style="left:98px;top:448px;width:130px;height:57px">Read More</a>
  <div class="hero-piece" role="img" aria-label="Photo of a tall amethyst geode sculpture on a round base" style="background:radial-gradient(ellipse at 50% 40%,rgba(80,45,140,.75),rgba(40,22,70,.35) 55%,transparent 75%)"></div>
</header>

<section class="about">
  <div class="photo-frame" role="img" aria-label="Photo of a green malachite sculpture on a turned base" style="left:98px;top:5px;width:467px;height:520px;background:radial-gradient(ellipse at 50% 45%,#1f4a34,#0b0b0b 70%)"></div>
  <h2 class="bar-heading" style="left:610px;top:90px">About Tidemark Vale Studios</h2>
  <div class="body-copy abs" style="left:636px;top:160px;width:466px">
    <p>The Tidemark Vale Studios or known to some as the "Ember Shell Crew" originally began 20 years ago when the founder of "Wyrm Bones" and the "Ember Eggs".</p>
    <p>The machine has since undergone many changes to what it is today.</p>
  </div>
  <a class="btn btn--caps" href="#" style="left:636px;top:385px;width:144px;height:56px">Read More</a>
</section>

<section class="gallery">
  <h2 class="center-heading" style="top:70px">Our Gallery</h2>
  <div class="underline" style="top:130px"></div>
  <svg class="arrow" style="left:30px;top:340px" viewBox="0 0 32 60" aria-hidden="true"><polyline points="28,4 4,30 28,56" fill="none" stroke="#fff" stroke-width="2"/></svg>
  <svg class="arrow" style="left:1138px;top:340px" viewBox="0 0 32 60" aria-hidden="true"><polyline points="4,4 28,30 4,56" fill="none" stroke="#fff" stroke-width="2"/></svg>

  <div class="card" style="left:100px">
    <div class="photo-frame frame-light" role="img" aria-label="Photo of a slender green stone sculpture" style="inset:0;width:310px;height:345px;background:radial-gradient(ellipse at 50% 45%,#1c3d2b,#0a0a0a 65%)"></div>
    <div class="card-title">NEMO ENIM IPSAM</div><div class="card-price">$150.00</div>
  </div>
  <div class="card" style="left:445px">
    <div class="photo-frame frame-light" role="img" aria-label="Photo of a twisting blue sodalite sculpture" style="inset:0;width:310px;height:345px;background:radial-gradient(ellipse at 50% 45%,#232c4f,#0a0a0a 65%)"></div>
    <div class="card-title">NEMO ENIM IPSAM</div><div class="card-price">$150.00</div>
  </div>
  <div class="card" style="left:790px">
    <div class="photo-frame frame-light" role="img" aria-label="Photo of an amber agate slab sculpture" style="inset:0;width:310px;height:345px;background:radial-gradient(ellipse at 50% 45%,#4a2a14,#0a0a0a 65%)"></div>
    <div class="card-title">NEMO ENIM IPSAM</div><div class="card-price">$150.00</div>
  </div>
</section>

<section class="videos">
  <div class="abs" role="img" aria-label="Video still of the artist working on a geode at a table" style="left:98px;top:108px;width:472px;height:307px;border:3px solid #888;background:linear-gradient(120deg,#8a8a86,#bdbab4 45%,#5e5246 80%,#2a2a2a)"></div>
  <svg class="abs" style="left:294px;top:222px" width="80" height="80" viewBox="0 0 80 80" aria-label="Play video" role="img">
    <circle cx="40" cy="40" r="36" fill="rgba(0,0,0,.25)" stroke="#fff" stroke-width="4"/>
    <polygon points="32,24 58,40 32,56" fill="#fff"/>
  </svg>
  <h2 class="bar-heading" style="left:610px;top:88px">Our Videos</h2>
  <div class="body-copy abs" style="left:636px;top:152px;width:466px">
    <p>After receiving an overwhelmingly positive reaction from his new machine Aren set out to find a Tidemark Vale Studios supplier. After experimenting with several different geode types.</p>
    <p>Aren realized that by far the most popular and consistently beautiful geodes were the Coconut Tidemark Vale Studios from Chihuahua, Mexico. And so it began.</p>
  </div>
  <a class="btn btn--caps" href="#" style="left:636px;top:385px;width:144px;height:56px">Read More</a>
</section>

<section class="testimonials">
  <div class="abs" role="img" aria-label="Darkened photo of two halves of an opened geode" style="inset:0;width:1200px;height:530px;background:radial-gradient(ellipse at 50% 55%,#3a3634,#1e1d1d 75%)"></div>
  <div class="vline" style="top:40px;height:55px"></div>
  <h2 class="center-heading" style="top:118px">Our Testimonials</h2>
  <svg class="arrow" style="left:30px;top:200px" viewBox="0 0 32 60" aria-hidden="true"><polyline points="28,4 4,30 28,56" fill="none" stroke="#fff" stroke-width="2"/></svg>
  <svg class="arrow" style="left:1138px;top:200px" viewBox="0 0 32 60" aria-hidden="true"><polyline points="4,4 28,30 4,56" fill="none" stroke="#fff" stroke-width="2"/></svg>
  <p class="quote">"Had an amazing time with you guys yesterday at WVF! This was my second year hatching an ember egg with you guys and I am addicted!! I can't wait for next years, I'll be saving for a really big one!"</p>
  <div class="quote-name">-Mara T</div>
  <a class="btn btn--caps" href="#" style="left:527px;top:347px;width:146px;height:56px;background:rgba(0,0,0,.35)">Load More</a>
  <div class="vline" style="top:433px;height:52px"></div>
</section>

<footer class="contact">
  <h2 class="center-heading" style="top:75px">Contact Us</h2>
  <div class="underline" style="top:135px"></div>
  <div class="contact-row">
    <div class="contact-item">
      <svg width="38" height="38" viewBox="0 0 38 38" aria-hidden="true"><circle cx="19" cy="19" r="17" fill="none" stroke="#fff" stroke-width="2"/><path d="M13 11c2-1 3 0 4 3s-1 3-1 4 2 4 4 5 2-1 4-1 3 2 2 4-3 2-6 0-8-6-9-10 0-4 2-5z" fill="#fff"/></svg>
      <span>(555) 014-2290</span>
    </div>
    <div class="contact-item">
      <svg width="38" height="38" viewBox="0 0 38 38" aria-hidden="true"><circle cx="19" cy="19" r="17" fill="none" stroke="#fff" stroke-width="2"/><rect x="11" y="13" width="16" height="12" fill="none" stroke="#fff" stroke-width="1.6"/><polyline points="11,13 19,20 27,13" fill="none" stroke="#fff" stroke-width="1.6"/></svg>
      <span>info@tidemarkvale.com</span>
    </div>
  </div>
  <nav class="foot-nav">
    <span>Home</span><span class="sep">|</span><span>About Us</span><span class="sep">|</span><span>New Sculptures</span><span class="sep">|</span><span>Sold Sculptures</span><span class="sep">|</span><span>Contact Us</span>
  </nav>
  <div class="foot-rule"></div>
  <div class="copyright">Copyrights @ 2018 Tidemark Vale Studios. All Rights Reserved.</div>
  <div class="social" aria-label="Social links"><span></span><span></span><span></span><span></span><span></span></div>
</footer>

</body>
</html>
```